Business Cards Needed for Innovative Healthcare Marketing Company

We are a marketing company focused on healthcare. Our company is all about rebranding yourself renewing your image and generating results. The phoenix stands for "reborn" or "rising" which we provide new brands for our clients we take their old brands and renew it with creativity and innovation. I am looking for a business card with color dimension. I have attached an example of a card I think has the look and feel of what I am trying to accomplish. I like that the card example has black and grey font colors, I like the font placement and the small logo, I really like the use of the colors on the right those are the colors of my logo. My logo is phoenix so maybe incorporating flames similar to that design. I would like the back a solid color maybe red with an opaque version of the logo and website. As a marketing company I am always open to creative liberty!

Target Market(s)

Doctors and business professionals.

Industry/Entity Type

Marketing

Contact Information for Business Card

Valcorne Health Care Marketing
Marla Tenwick- CEO
#(512)638-2974
email-marla@valcorne.com
website- valcorne.com

Font styles to use
Sans Serif

Colors
ec1f27
f37122
ffc214
fbed22
fbf289
f04a50

Requirements
Must have
• The logo and required information
Nice to have
• icons by the information
Should not have
• child like font

```html
<!DOCTYPE html>
<html lang="en">
<head>
<meta charset="utf-8">
<title>Valcorne Health Care Marketing – Business Card</title>
<link rel="stylesheet" href="https://fonts.googleapis.com/css2?family=Source+Sans+3:wght@300;400;600&display=swap">
<style>
  :root {
    --page-bg: #e9e6e3;
    --card-white: #ffffff;
    --brand-red: #a3201f;
    --name-orange: #c3450f;
    --ink: #2b2b2b;
    --flame-orange: #f37122;
    --flame-amber: #f7941d;
    --flame-deep: #a8201a;
    --on-dark: #ffffff;
    --rule-soft: rgba(163, 32, 31, 0.45);
  }
  * { box-sizing: border-box; margin: 0; padding: 0; }
  html, body {
    width: 1200px; height: 900px; overflow: hidden;
    background: var(--page-bg);
    font-family: "Source Sans 3", sans-serif;
  }
  .canvas { position: relative; width: 1200px; height: 900px; }

  .card {
    position: absolute;
    overflow: hidden;
    box-shadow: 0 6px 18px rgba(0,0,0,0.18);
  }

  /* Front */
  .card-front { left: 78px; top: 34px; width: 588px; height: 365px; background: var(--card-white); }
  .front-artwork {
    position: absolute; top: 0; right: 0; width: 190px; height: 100%;
    background: linear-gradient(160deg, var(--flame-orange) 0%, var(--flame-deep) 45%, var(--flame-amber) 100%);
  }
  .brand-lockup { position: absolute; left: 30px; top: 46px; display: flex; align-items: center; gap: 14px; }
  .brand-dot { width: 56px; height: 56px; border-radius: 50%; background: var(--flame-orange); flex: none; }
  .brand-name { color: var(--brand-red); font-weight: 300; line-height: 1; }
  .brand-name .word { display: block; font-size: 44px; letter-spacing: 1px; padding-bottom: 6px; border-bottom: 1px solid var(--rule-soft); }
  .brand-name .sub { display: block; font-size: 15.5px; letter-spacing: 0.8px; margin-top: 6px; }

  .person { position: absolute; left: 28px; top: 186px; }
  .person-name { font-size: 21px; font-weight: 600; color: var(--name-orange); line-height: 1.2; }
  .person-role { font-size: 15px; color: var(--ink); margin-top: 2px; }

  .contact-list { position: absolute; left: 28px; top: 266px; list-style: none; }
  .contact-item {
    display: flex; align-items: center; gap: 12px;
    font-size: 15.5px; color: var(--ink); height: 25px;
  }
  .contact-icon { width: 12px; height: 12px; flex: none; }

  /* Back */
  .card-back {
    left: 388px; top: 505px; width: 566px; height: 352px;
    background: var(--flame-orange);
  }
  .back-artwork {
    position: absolute; inset: 0;
    background: linear-gradient(135deg, var(--flame-amber) 0%, var(--flame-orange) 40%, #d4501c 70%, var(--flame-deep) 100%);
  }
  .back-brand {
    position: absolute; left: 0; right: 0; top: 124px;
    display: flex; flex-direction: column; align-items: center;
    color: var(--on-dark); font-weight: 300; line-height: 1;
  }
  .back-brand .word { font-size: 70px; letter-spacing: 2px; padding: 0 4px 12px; border-bottom: 1px solid rgba(255,255,255,0.7); }
  .back-brand .sub { font-size: 23px; letter-spacing: 1.5px; margin-top: 14px; }
  .back-site {
    position: absolute; left: 0; right: 0; bottom: 26px;
    text-align: center; color: var(--on-dark); opacity: 0.85;
    font-size: 15px; font-weight: 400; letter-spacing: 1px;
  }
</style>
</head>
<body>
<main class="canvas">

  <section class="card card-front" aria-label="Business card front">
    <div class="front-artwork" role="img" aria-label="Flowing orange and red flame artwork"></div>

    <div class="brand-lockup">
      <span class="brand-dot"></span>
      <p class="brand-name"><span class="word">VALCORNE</span><span class="sub">HEALTH CARE MARKETING</span></p>
    </div>

    <div class="person">
      <p class="person-name">Marla Tenwick</p>
      <p class="person-role">CEO</p>
    </div>

    <ul class="contact-list">
      <li class="contact-item">
        <svg class="contact-icon" viewBox="0 0 12 12" aria-hidden="true"><path d="M2.5 1 L4.5 1 L5.3 3.6 L4 4.6 C4.7 6 6 7.3 7.4 8 L8.4 6.7 L11 7.5 L11 9.5 C11 10.4 10.3 11 9.5 11 C5 10.6 1.4 7 1 2.5 C1 1.7 1.6 1 2.5 1 Z" fill="#e0651f"/></svg>
        (512)638-2974
      </li>
      <li class="contact-item">
        <svg class="contact-icon" viewBox="0 0 12 12" aria-hidden="true"><rect x="0.5" y="2.5" width="11" height="7.5" fill="#e0651f"/><path d="M0.5 2.5 L6 7 L11.5 2.5" stroke="#fff" stroke-width="1" fill="none"/></svg>
        marla@valcorne.com
      </li>
      <li class="contact-item">
        <svg class="contact-icon" viewBox="0 0 12 12" aria-hidden="true"><circle cx="6" cy="6" r="5.5" fill="#e0651f"/><circle cx="6" cy="6" r="2" fill="#fff"/></svg>
        www.valcorne.com
      </li>
    </ul>
  </section>

  <section class="card card-back" aria-label="Business card back">
    <div class="back-artwork" role="img" aria-label="Flowing orange and red flame artwork"></div>
    <p class="back-brand"><span class="word">VALCORNE</span><span class="sub">HEALTH CARE MARKETING</span></p>
    <p class="back-site">www.valcorne.com</p>
  </section>

</main>
</body>
</html>
```